We need a package design for a dietary supplement.

We need a package design for a dietary supplement - throwable tablets - Senegalese acacia fiber with pineapple flavor.
New name BrightOrbit.
Remember the packaging is a white jar, a magenta cap, a sticker, and a cardboard box. We want to change the name to: BrightOrbit (if you have a better idea for the name, just tell me) and refresh the packaging.
Product description:
> Contributes to improving the functioning of the digestive system.
> Boosts metabolism, controls appetite and supports weight loss.
> Helps maintain normal blood sugar levels.
> Regulates cholesterol levels
> 100% natural ingredients in the form of chewable tablets.
It has many beneficial health benefits:
> Cleanses the body of toxins,
> Helps with constipation and bloating,
> Facilitates defecation,
> Regulates cholesterol levels (by eliminating bile acids from the intestine),
> Adds energy,
> Improves metabolism,
> reduces appetite,
> Improves the work of the digestive system,
> It can help to get rid of the unpleasant smell from the mouth,
> Improves well-being,
> Regular intake can lead to weight loss,
> It works gently and does not cause side effects,
> Delays the aging process,
> Improves the appearance of the skin
This all-natural dietary supplement supports heart health, helps maintain blood sugar levels, soothes irritable bowel syndrome, and improves overall gut health.

100% natural, vegan product, no added sugars, no added salt. It has only 2 ingredients: Cenegal acacia and pineapple juice.

We are changing the name and packaging for our product called KestroNuma. Photos attached, packaging grid attached, samples of our other packaging attached.
*Packaging in Dutch

Target Market(s)

Netherlands

Industry/Entity Type

dietary supplements

Colors

Designer to choose colors to be used in the design.

Requirements
Must have
• Modern and inspire patient confidence.
Nice to have
• Good, natural, healthy
Should not have
• It should not clearly indicate that it has a slimming effect, as in the kestronuma project

```html
<!DOCTYPE html>
<html lang="en">
<head>
<meta charset="utf-8">
<title>BrightOrbit – Label</title>
<link rel="stylesheet" href="https://fonts.googleapis.com/css2?family=Montserrat:wght@200;300;400;700;800&family=Josefin+Sans:wght@300;400&display=swap">
<style>
  :root {
    --page: #ffffff;
    --ink-black: #141414;
    --ink-black-light: #3a3a3a;
    --leaf-green: #5b7a44;
    --leaf-green-soft: #4c6a37;
    --forest-green: #3c5427;
    --forest-green-deep: #2f461e;
    --acacia-green: #3d5e2b;
    --text-light: #f4f4f4;
    --line-dark: #111111;
  }
  * { margin: 0; padding: 0; box-sizing: border-box; }
  html, body {
    width: 1200px; height: 1200px; overflow: hidden;
    background: var(--page);
  }
  .label {
    position: absolute; left: 120px; top: 66px;
    width: 960px; height: 1064px; overflow: hidden;
    font-family: "Montserrat", sans-serif;
    color: var(--text-light);
  }
  .label__head {
    position: absolute; left: 0; top: 0; width: 100%; height: 523px;
    background: linear-gradient(100deg, var(--ink-black-light) 0%, var(--ink-black) 45%, #0e0e0e 100%);
  }
  .label__claims {
    position: absolute; left: 0; top: 523px; width: 100%; height: 274px;
    background: linear-gradient(100deg, var(--leaf-green) 0%, var(--leaf-green-soft) 60%, var(--leaf-green) 100%);
  }
  .label__foot {
    position: absolute; left: 0; top: 797px; width: 100%; height: 267px;
    background: linear-gradient(100deg, var(--forest-green) 0%, var(--forest-green-deep) 100%);
  }
  .brand {
    position: absolute; left: 68px; top: 118px;
    font-weight: 800; font-size: 48px; letter-spacing: 0.01em;
    color: var(--text-light);
  }
  .count {
    position: absolute; left: 668px; top: 124px;
    font-family: "Josefin Sans", sans-serif;
    font-weight: 300; font-size: 37px; letter-spacing: 0.04em;
  }
  .product-name {
    position: absolute; left: 64px; top: 283px;
    font-size: 116px; line-height: 1; letter-spacing: 0.005em; white-space: nowrap;
  }
  .product-name__light { font-weight: 200; }
  .product-name__bold { font-weight: 700; }
  .product-type {
    position: absolute; left: 68px; top: 422px;
    font-weight: 400; font-size: 37px; letter-spacing: 0.22em;
    color: var(--acacia-green); white-space: nowrap;
  }
  .claims-text {
    position: absolute; left: 54px; top: 598px;
    font-family: "Josefin Sans", sans-serif;
    font-weight: 400; font-size: 26px; line-height: 34px; letter-spacing: 0.05em;
    text-transform: uppercase; white-space: nowrap;
  }
  .claims-text span { display: block; }
  .seal {
    position: absolute; left: 748px; top: 706px; width: 172px; height: 172px;
  }
  .category {
    position: absolute; left: 62px; top: 846px;
    font-family: "Josefin Sans", sans-serif;
    font-weight: 400; font-size: 29px; letter-spacing: 0.02em;
  }
  .divider {
    position: absolute; left: 52px; top: 929px; width: 456px; height: 2px;
    background: var(--line-dark);
  }
  .badges {
    position: absolute; left: 58px; top: 972px;
    display: flex; align-items: center;
    font-family: "Josefin Sans", sans-serif;
    font-weight: 400; font-size: 29px; letter-spacing: 0.01em; white-space: nowrap;
  }
  .badges__item--vegan { margin-left: 28px; }
  .badges__dot {
    width: 14px; height: 14px; border-radius: 50%;
    background: var(--line-dark); margin-left: 50px;
  }
</style>
</head>
<body>
  <main class="label">
    <section class="label__head">
      <div class="brand">NORDAVERA</div>
      <div class="count">100 CAPS</div>
      <h1 class="product-name"><span class="product-name__light">BRIGHT</span><span class="product-name__bold">ORBIT</span></h1>
      <div class="product-type">SENEGALESE ACACIA FIBER</div>
    </section>

    <section class="label__claims"></section>
    <section class="label__foot"></section>

    <p class="claims-text">
      <span>All-natural dietary supplement supports</span>
      <span>heart health, helps maintain blood sugar</span>
      <span>levels, soothes irritable bowel syndrome,</span>
      <span>and improves overall gut health.</span>
    </p>

    <svg class="seal" viewBox="0 0 172 172" aria-hidden="true">
      <circle cx="86" cy="86" r="82" fill="#3c5427" stroke="#111" stroke-width="2"/>
      <circle cx="86" cy="86" r="43" fill="none" stroke="#111" stroke-width="2"/>
    </svg>

    <div class="category">DIETARY SUPPLEMENT</div>
    <div class="divider"></div>
    <div class="badges">
      <span class="badges__item">NO ADDED SUGAR OR SALT</span>
      <span class="badges__dot"></span>
      <span class="badges__item badges__item--vegan">VEGAN PRODUCT</span>
    </div>
  </main>
</body>
</html>
```